Brightarc Orthodontics appointment card design

I need appointment cards/ business cards made. Front will be Logo, name, title, email, phone number and location (5263 Walnut Hollow Pkwy, Ste 412, Concord, NC 28027) . the back should have an appointment card (name, time, date) and also 3 addresses listed with a check box so we can check to which location they are going.
Dale Fenwick Orthodontics
- 6735 Orchard Street, Ste 514, Harrisburg, NC 28075
- 3647 Ridgeway Drive NE, Ste 810, Concord, NC 28025
- 2917 Thornbury Corporate Drive, Ste 605, Charlotte, NC 28277
Business card can be horizontal or vertical in Design.
I need to be able to edit it to update and add new employees

Requirements
Must have
• Front:
• - Logo
• - Name & Title (able to be edited)
• - phone (704-555-0186) & Email (need to be able to edit)
• - Address: 5263 Walnut Hollow Pkwy, Ste 412
• Concord, NC 28027
• Back:
• Appointment Card design:
• - Name, time, Date
• - 3 locations w/ a check box so the patient knows where to go:
• Dale Fenwick Orthodontics
• - 6735 Orchard Street, Ste 514, Harrisburg, NC 28075
• - 3647 Ridgeway Drive NE, Ste 810, Concord, NC 28025
• - 2917 Thornbury Corporate Drive, Ste 605, Charlotte, NC 28277

```html
<!DOCTYPE html>
<html lang="en">
<head>
<meta charset="utf-8">
<title>Brightarc Orthodontics – Appointment &amp; Business Card</title>
<link rel="stylesheet" href="https://fonts.googleapis.com/css2?family=Roboto:wght@400;500;700&display=swap">
<style>
  :root {
    --brand-blue: #1a78c2;
    --brand-blue-dark: #1565a8;
    --ink: #3d3d3d;
    --ink-soft: #555555;
    --rule: #4a4a4a;
    --card: #ffffff;
    --backdrop: #e6e7e9;
  }
  * { box-sizing: border-box; margin: 0; padding: 0; }
  html, body {
    width: 1200px; height: 1000px; overflow: hidden;
    background: var(--backdrop);
    font-family: "Roboto", Arial, sans-serif;
    color: var(--ink);
  }
  .stage { position: relative; width: 1200px; height: 1000px; }

  .card {
    position: absolute;
    width: 720px; height: 410px;
    background: var(--card);
    border-radius: 28px;
    overflow: hidden;
    box-shadow: 0 10px 30px rgba(0,0,0,0.12);
  }

  /* ---------- Appointment side ---------- */
  .appointment { left: 400px; top: 50px; }
  .appointment .top-band {
    position: absolute; left: 0; top: 0; width: 100%; height: 14px;
    background: var(--brand-blue);
  }
  .appointment .heading {
    position: absolute; left: 38px; top: 44px;
    font-size: 20px; font-weight: 700; color: var(--brand-blue);
  }
  .field { position: absolute; display: flex; align-items: flex-end; font-size: 14px; color: var(--ink-soft); }
  .field .line { flex: 1; border-bottom: 1.5px solid var(--rule); margin-left: 8px; height: 1px; }
  .field-name { left: 38px; top: 92px; width: 390px; }
  .field-date { left: 38px; top: 130px; width: 390px; }
  .field-time { left: 38px; top: 172px; width: 644px; }
  .field-time .line.lead { flex: 0 0 300px; margin: 0 8px 0 0; }

  .meridiem { position: absolute; right: 38px; top: 200px; display: flex; gap: 22px; font-size: 14px; color: var(--ink-soft); }
  .meridiem label { display: flex; align-items: center; gap: 6px; }

  .check {
    display: inline-block; width: 15px; height: 15px;
    border: 1.5px solid var(--brand-blue); background: #fff;
  }

  .appointment .wordmark {
    position: absolute; right: 38px; top: 64px; width: 220px;
    text-align: right; font-size: 30px; line-height: 1.05;
    font-weight: 700; color: var(--brand-blue);
  }

  .practice-name {
    position: absolute; left: 0; width: 100%; top: 238px; text-align: center;
    font-size: 20px; font-weight: 700; color: var(--brand-blue);
  }
  .practice-name span { font-size: 16px; font-weight: 400; color: var(--ink-soft); }

  .locations {
    position: absolute; left: 30px; right: 30px; top: 280px;
    display: grid; grid-template-columns: 1fr 1fr 1fr; gap: 20px;
  }
  .location { text-align: center; font-size: 13px; line-height: 1.35; color: var(--ink-soft); }
  .location .check { margin-bottom: 8px; }

  /* ---------- Business side ---------- */
  .business { left: 120px; top: 540px; }
  .business .corner-square {
    position: absolute; left: 0; top: 30px; width: 34px; height: 40px;
    background: var(--brand-blue);
  }
  .business .person { position: absolute; left: 50px; top: 32px; }
  .business .person-name { font-size: 21px; font-weight: 700; color: var(--brand-blue); letter-spacing: 0.3px; }
  .business .person-title { font-size: 14px; color: var(--ink-soft); margin-top: 2px; }

  .contact { position: absolute; left: 50px; top: 250px; font-size: 16px; line-height: 1.4; color: var(--ink); }
  .contact .address { margin-bottom: 6px; }
  .contact .row { display: flex; align-items: center; gap: 8px; }
  .contact svg { width: 14px; height: 14px; fill: var(--brand-blue); }

  .business .wordmark {
    position: absolute; right: 50px; bottom: 50px; width: 330px;
    text-align: right; font-size: 52px; line-height: 1.05;
    font-weight: 700; color: var(--brand-blue);
  }
</style>
</head>
<body>
<main class="stage">

  <section class="card appointment" aria-label="Appointment card">
    <div class="top-band"></div>
    <h2 class="heading">Next Appointment</h2>

    <div class="field field-name">Name<span class="line"></span></div>
    <div class="field field-date">Date<span class="line"></span></div>
    <div class="field field-time"><span class="line lead"></span>Time<span class="line"></span></div>

    <div class="meridiem">
      <label><span class="check"></span>AM</label>
      <label><span class="check"></span>PM</label>
    </div>

    <div class="wordmark">Brightarc Orthodontics</div>

    <p class="practice-name">Dale Fenwick <span>Orthodontics</span></p>

    <div class="locations">
      <div class="location"><span class="check"></span><br>6735 Orchard Street, Ste 514,<br>Harrisburg, NC 28075</div>
      <div class="location"><span class="check"></span><br>3647 Ridgeway Drive NE, Ste 810,<br>Concord, NC 28025</div>
      <div class="location"><span class="check"></span><br>2917 Thornbury Corporate Drive,<br>Ste 605, Charlotte, NC 28277</div>
    </div>
  </section>

  <section class="card business" aria-label="Business card">
    <div class="corner-square"></div>
    <div class="person">
      <p class="person-name">DALE FENWICK</p>
      <p class="person-title">Orthodontics</p>
    </div>

    <div class="contact">
      <p class="address">5263 Walnut Hollow Pkwy,<br>Ste 412 - Concord, NC 28027</p>
      <p class="row">
        <svg viewBox="0 0 24 24" aria-hidden="true"><path d="M6.6 10.8a15 15 0 0 0 6.6 6.6l2.2-2.2a1 1 0 0 1 1-.25 11.4 11.4 0 0 0 3.6.57 1 1 0 0 1 1 1V20a1 1 0 0 1-1 1A17 17 0 0 1 3 4a1 1 0 0 1 1-1h3.5a1 1 0 0 1 1 1c0 1.25.2 2.45.57 3.57a1 1 0 0 1-.25 1z"/></svg>
        704-555-0186
      </p>
      <p class="row">
        <svg viewBox="0 0 24 24" aria-hidden="true"><path d="M2 5h20v14H2z M3.5 6.5 12 13l8.5-6.5" /><path d="M2 5h20v14H2V5zm2 2v.4l8 6 8-6V7H4z" fill="#fff"/></svg>
        dale.fenwick@brightarcmail.com
      </p>
    </div>

    <div class="wordmark">Brightarc Orthodontics</div>
  </section>

</main>
</body>
</html>
```